Business Card Design

I give lessons and clinics for dressage riders
I would like the design to be an outline (with broad lines) of a dressage horse and rider with in background of whole card with print over top tan or parchment card with burgundy print

Industry/Entity Type

Business

Contact Information for Business Card

Dale Ferrin
612-374-2059
Classical dressage training for the modern American
Clinics, lessons, training level -Prix St. George

Requirements
Must have
• broad lined outline of dressage horse and rider

```html
<!DOCTYPE html>
<html lang="en">
<head>
<meta charset="utf-8">
<title>Dale Ferrin – Classical Dressage Training</title>
<link rel="stylesheet" href="https://fonts.googleapis.com/css2?family=Cinzel:wght@500&display=swap">
<style>
  :root {
    --parchment: #efe6b3;
    --parchment-light: #f5efc6;
    --parchment-shade: #e4d79c;
    --burgundy: #4b1a2d;
    --burgundy-soft: rgba(75, 26, 45, 0.28);
    --burgundy-faint: rgba(75, 26, 45, 0.10);
  }
  * { margin: 0; padding: 0; box-sizing: border-box; }
  html, body {
    width: 1200px;
    height: 693px;
    overflow: hidden;
    background: var(--parchment);
  }
  .business-card {
    position: relative;
    width: 1200px;
    height: 693px;
    overflow: hidden;
    background:
      repeating-linear-gradient(90deg, rgba(255,255,255,0.10) 0 2px, rgba(0,0,0,0.025) 2px 4px),
      radial-gradient(ellipse at 50% 45%, var(--parchment-light) 0%, var(--parchment) 55%, var(--parchment-shade) 100%);
    color: var(--burgundy);
    font-family: "Cinzel", "Trajan Pro", serif;
    font-weight: 500;
  }
  .horse-and-rider {
    position: absolute;
    left: 318px;
    top: 52px;
    width: 575px;
    height: 410px;
    border-radius: 46% 40% 38% 44% / 42% 46% 40% 44%;
    background: radial-gradient(ellipse at 50% 50%, var(--burgundy-soft) 0%, var(--burgundy-faint) 70%, transparent 100%);
  }
  .contact-line {
    position: absolute;
    left: 0;
    width: 100%;
    text-align: center;
    white-space: nowrap;
  }
  .name-and-phone {
    top: 515px;
    font-size: 52px;
    letter-spacing: 3px;
    word-spacing: 6px;
  }
  .name-and-phone .phone { margin-left: 22px; letter-spacing: 4px; }
  .tagline {
    top: 585px;
    font-size: 31px;
    letter-spacing: 1px;
  }
  .services {
    top: 630px;
    font-size: 31px;
    letter-spacing: 1.5px;
  }
</style>
</head>
<body>
  <main class="business-card">
    <div class="horse-and-rider" role="img" aria-label="Broad-lined burgundy illustration of a dressage rider on a horse at an extended trot"></div>
    <p class="contact-line name-and-phone"><span class="name">Dale Ferrin</span><span class="phone">612-374-2059</span></p>
    <p class="contact-line tagline">Classical dressage training for the modern American</p>
    <p class="contact-line services">Clinics, lessons, training level -Prix St. George</p>
  </main>
</body>
</html>
```